Letterhead and matching envelope design for a dental office

We need a new stationary design, letterhead and envelope #10, for a dental office in Denver area. We are called Bright Harbor Dental. We want a simple and minimalistic design but not a boring design. I wish to have one good point that makes it look professional. I have attached our logo. Feel free to use either one. I want the design for letterhead and envelope look like a "matching pair" but not look the same. The envelope doesn't have to be white and it will have an address window on bottom left.

Target Market(s)

everyone who visits dentist (adults)

Industry/Entity Type

Dental

Font styles to use
Other font styles liked:
• close to font on logo or something that matches well

Requirements
Must have
• professional
• simple, minimalistic
• unique point that stands out
Nice to have
• matching but not same design for letterhead and envelope
Should not have
• not look like all the other boring designs
• no flowery, distracting feats

```html
<!DOCTYPE html>
<html lang="en">
<head>
<meta charset="utf-8">
<title>Bright Harbor Dental – #10 Envelope</title>
<link rel="stylesheet" href="https://fonts.googleapis.com/css2?family=Open+Sans:wght@400;600&display=swap">
<style>
  :root {
    --brand-green: #3bb54a;
    --brand-green-pale: #a9d9ad;
    --rule-green: #e3f1e4;
    --paper: #ffffff;
    --ink: #2b2b2b;
    --backdrop: #ecebe8;
  }
  * { margin: 0; padding: 0; box-sizing: border-box; }
  html, body {
    width: 1200px; height: 800px; overflow: hidden;
    background: var(--backdrop);
    font-family: "Open Sans", Arial, sans-serif;
  }
  .canvas { position: relative; width: 1200px; height: 800px; }
  .envelope-shape { position: absolute; left: 0; top: 0; }
  .flap-name {
    position: absolute; left: 450px; top: 160px; width: 300px;
    text-align: center; color: var(--paper);
    font-size: 17px; font-weight: 600; letter-spacing: 0.5px;
  }
  .return-name {
    position: absolute; left: 155px; top: 318px; width: 170px;
    display: flex; align-items: center; gap: 10px;
    color: var(--brand-green); font-size: 21px; font-weight: 600; line-height: 1.2;
  }
  .return-name .mark-dot {
    flex: none; width: 16px; height: 16px; border-radius: 50%;
    background: var(--brand-green);
  }
  .sender {
    position: absolute; right: 154px; top: 302px;
    text-align: right; color: var(--ink); font-size: 16px; line-height: 22px;
  }
  .sender .sender-name { color: var(--brand-green); }
  .sender .contacts { margin-top: 13px; }
  .contact-line { display: flex; justify-content: flex-end; align-items: center; gap: 6px; height: 25px; }
  .contact-icon {
    width: 19px; height: 19px; border-radius: 50%;
    background: var(--brand-green); display: flex; align-items: center; justify-content: center;
  }
  .divider {
    position: absolute; left: 155px; top: 457px; width: 890px; height: 1px;
    background: var(--rule-green);
  }
  .website {
    position: absolute; left: 125px; top: 647px; width: 937px;
    text-align: center; color: var(--brand-green);
    font-size: 16px; letter-spacing: 2px;
  }
</style>
</head>
<body>
<main class="canvas">
  <svg class="envelope-shape" width="1200" height="800" viewBox="0 0 1200 800" aria-hidden="true">
    <path class="flap" fill="var(--brand-green)"
      d="M125,277 L146,232 Q153,218 170,214 L560,116 Q600,106 640,116 L1040,214 Q1060,220 1066,240 L1075,277 Z"/>
    <rect class="envelope-body" x="125" y="277" width="950" height="411" fill="var(--paper)"/>
    <rect class="edge-band-top" x="1062" y="277" width="13" height="172" fill="var(--brand-green)"/>
    <path class="edge-band-notch" fill="var(--brand-green)" d="M1062,449 L1075,449 L1075,462 Z"/>
    <path class="edge-band-bottom" fill="var(--brand-green-pale)" d="M1075,462 L1062,449 L1062,688 L1075,688 Z"/>
    <path class="edge-notch-white" fill="var(--paper)" d="M1062,449 L1072,457 L1062,466 Z"/>
  </svg>

  <div class="flap-name">Bright Harbor Dental</div>

  <div class="return-name"><span class="mark-dot"></span><span>Bright Harbor Dental</span></div>

  <address class="sender" style="font-style:normal">
    <div class="sender-name">Bright Harbor Dental</div>
    <div>4820 Lantern Ridge Dr,</div>
    <div>Suite 210 Arvada, CO 80002</div>
    <div class="contacts">
      <div class="contact-line">
        <span>720-555-0143</span>
        <span class="contact-icon">
          <svg width="11" height="11" viewBox="0 0 24 24" aria-hidden="true"><path fill="#fff" d="M6.6 10.8c1.4 2.8 3.8 5.1 6.6 6.6l2.2-2.2c.3-.3.7-.4 1-.2 1.1.4 2.3.6 3.6.6.6 0 1 .4 1 1V20c0 .6-.4 1-1 1C10.6 21 3 13.4 3 4c0-.6.4-1 1-1h3.5c.6 0 1 .4 1 1 0 1.3.2 2.5.6 3.6.1.3 0 .7-.2 1z"/></svg>
        </span>
      </div>
      <div class="contact-line">
        <span>info@brightharbordental.com</span>
        <span class="contact-icon">
          <svg width="11" height="9" viewBox="0 0 22 16" aria-hidden="true"><rect x="1" y="1" width="20" height="14" rx="1" fill="#fff"/><path d="M1 2 L11 9 L21 2" fill="none" stroke="var(--brand-green)" stroke-width="1.6"/></svg>
        </span>
      </div>
    </div>
  </address>

  <div class="divider"></div>

  <div class="website">www.brightharbordental.com</div>
</main>
</body>
</html>
```